$5 Quest Website Required

I am looking for someone to develop a website akin to the simplicity of www.boxlantern.example with a video in the center or a tab that permits one to "Accept the Challenge."

Incorporates our logo and is used to promote our "$5 Quest Program."

Please see attachments, but we are igniting entrepreneurial spirit among our nation's youth through this interactive and intensive program!

There should be a way to navigate to other sections of the site including:

About
Why
Request $5 Quest Packet
Success Stories
Partners
Link to Norvik Holdings
Updates

Thanks to all in advance!

Looking forward to working with you!

Good feel of what we are looking for in terms of "feel"

http://www.thebrightripple.example/

Thank you,

RB

Please make note of this website, we are going for a feel that is akin to this and less modern and professional...more abstract and interactive...but of course include space for our video:

Colors, feel, imagery, is great. Keep your formats, but bring on the feel!

Thank you all for your hard work and patience.

Thank you all for your hard work thus far.

Meanwhile, please understand that the $5 Quest is young, youthful, full of challenge and vitality, it is a competition among students from high school and universities.  The websites you have delivered are too corporate, stale, and standard.  I'm looking for something that is fresh, different, like www.thebrightripple.example.

Symbols, cartoonish, but serious, down to business and save the world one $5 bill at a time.  The logo can be used as a theme...the colors, the feel.

Video space for explanation on the $5 Quest front and center.  With leaves, $ signs, colorful colors, etc.

Visual needs to be compelling to Join the Challenge! Although Norvik Holdings and the tree is a parent company; $5 Quest is separate and Norvik Holdings should only be mentioned as a link.

PixelHarbor.example in regard to simplicity; and www.thebrightripple.example in terms of style.

Thank you,

Raphael

Like the designs that have been submitted; we are almost there.

Target Market(s)

Professors, students, teachers, parents and NGO leaders who wish to use our program as a way to inspire leadership/entrepreneurship/fundraise for their causes.

Requirements
Must have
• Place for the video, front and center
Include logo
Forsight for blogging, message, etc.
Nice to have
• Plan "buckets" to include"
Explanation Video
Two pamphlets
Contract
FAQs
Website with Blog, voting, registration, video upload, etc.
Flyer perfected
Parable...symbol of our life
Photos
Stats included
Testimonials
Organizations that have used (TKWLM, North Brook Lodge, Marlowton High)
Sponsors (Open Lantern, Copperleaf Learningfield)
Photos from events

I understand this takes coding and such, but want you to be aware of the long term vision for it!

```html
<!DOCTYPE html>
<html lang="en">
<head>
<meta charset="utf-8">
<title>$5 Quest</title>
<link href="https://fonts.googleapis.com/css2?family=Roboto+Condensed:wght@400;500;700&family=Arimo:wght@400&display=swap" rel="stylesheet">
<style>
  :root {
    --orange: #fea602;
    --green: #08893a;
    --green-dark: #06702f;
    --lime: #d6e423;
    --lime-light: #eef57a;
    --nav-active: #e8f03a;
    --ink: #3f3f3f;
    --white: #ffffff;
    --mint: #dff1e6;
    --butter: #f4f7d6;
  }
  * { box-sizing: border-box; margin: 0; padding: 0; }
  html, body { width: 1064px; height: 1200px; overflow: hidden; background: var(--white); }
  body { font-family: "Roboto Condensed", sans-serif; color: var(--ink); }
  .stage { position: relative; width: 1064px; height: 1200px; overflow: hidden; }

  .leaf-ring {
    position: absolute; left: 10px; top: 40px; width: 1044px; height: 1140px; border-radius: 50%;
    background: radial-gradient(ellipse at center, var(--mint) 0%, var(--mint) 48%, var(--butter) 68%, rgba(255,255,255,0) 72%);
  }

  .page-oval {
    position: absolute; left: 165px; top: 133px; width: 736px; height: 926px;
    border-radius: 50%; background: var(--white); overflow: hidden;
    box-shadow: 0 0 0 2px #e4e4e4, 0 6px 18px rgba(0,0,0,0.25);
  }
  .hero-band {
    position: absolute; left: 0; top: 243px; width: 100%; height: 552px; background: var(--orange);
  }

  .utility-links { position: absolute; top: 133px; left: 706px; display: flex; gap: 24px; align-items: center; }
  .utility-links a { font-size: 15px; font-weight: 500; color: #222; text-decoration: none; letter-spacing: 0.3px; }
  .utility-links .language {
    background: var(--lime); padding: 4px 10px; font-size: 13px; font-weight: 700; display: flex; gap: 8px; align-items: center;
  }

  .brand { position: absolute; left: 320px; top: 198px; width: 450px; display: flex; align-items: center; justify-content: center; gap: 18px; }
  .brand-dot { width: 92px; height: 92px; border-radius: 50%; background: var(--green); }
  .brand-name { font-family: "Arimo", sans-serif; font-size: 78px; color: #555; line-height: 1; }

  .main-nav { position: absolute; left: 128px; top: 322px; width: 806px; height: 54px; }
  .main-nav svg { position: absolute; inset: 0; }
  .main-nav ul { position: absolute; inset: 0; list-style: none; display: flex; align-items: center; justify-content: center; gap: 20px; padding-left: 6px; }
  .main-nav a { color: var(--white); text-decoration: none; font-size: 19px; font-weight: 500; letter-spacing: 0.2px; }
  .main-nav a.current { color: var(--nav-active); }

  .welcome { position: absolute; left: 202px; top: 396px; width: 660px; text-align: center; }
  .welcome h1 { font-size: 21px; font-weight: 500; color: var(--white); letter-spacing: 0.3px; }
  .welcome p { margin-top: 14px; text-align: left; font-family: "Arimo", sans-serif; font-size: 13.4px; line-height: 19px; color: #3a2a00; }

  .video-frame {
    position: absolute; left: 350px; top: 487px; width: 363px; height: 302px;
    background: var(--white); border: 4px solid #e6e6e6; outline: 3px solid var(--white);
    box-shadow: 0 14px 14px -8px rgba(0,0,0,0.35);
  }
  .play-button { position: absolute; left: 118px; top: 62px; width: 120px; height: 120px; border-radius: 50%;
    background: radial-gradient(circle at 50% 30%, #4a4a4a, #111 75%); }
  .play-button svg { position: absolute; left: 44px; top: 34px; }
  .video-label { position: absolute; top: 208px; width: 100%; text-align: center; font-size: 23px; font-weight: 500; color: #222; }
  .video-label::after { content: "WATCH VIDEO"; display: block; transform: scaleY(-1); opacity: 0.12; line-height: 0.7; }

  .cta-rule { position: absolute; left: 220px; top: 856px; width: 625px; border-top: 2px dashed #333; }
  .cta-button { position: absolute; left: 356px; top: 831px; width: 349px; height: 52px; text-decoration: none; }
  .cta-button svg { position: absolute; inset: 0; }
  .cta-button span { position: absolute; inset: 0; display: flex; align-items: center; justify-content: center; font-size: 23px; color: #3d4a1a; }

  .site-footer { position: absolute; left: 382px; top: 958px; width: 300px; text-align: center; }
  .footer-brand { display: inline-flex; align-items: center; gap: 6px; }
  .footer-brand .brand-dot { width: 22px; height: 22px; }
  .footer-brand .brand-name { font-size: 22px; color: var(--green-dark); }
  .site-footer small { display: block; margin-top: 22px; font-family: "Arimo", sans-serif; font-size: 12.5px; color: #333; }
</style>
</head>
<body>
<div class="stage">
  <div class="leaf-ring" role="img" aria-label="Ring of soft green and pale yellow leaves surrounding the page"></div>

  <div class="page-oval">
    <section class="hero-band" role="img" aria-label="Faint background diagram of the quest stages from idea to reward"></section>
  </div>

  <nav class="utility-links">
    <a href="#">FAQ</a>
    <a href="#">SIGNIN</a>
    <a href="#" class="language">LANGUAGE
      <svg width="11" height="9" viewBox="0 0 11 9"><path d="M0 0 H11 L5.5 9 Z" fill="#111"/></svg></a>
  </nav>

  <div class="brand">
    <span class="brand-dot"></span>
    <span class="brand-name">$5 Quest</span>
  </div>

  <nav class="main-nav">
    <svg viewBox="0 0 806 54" width="806" height="54" aria-hidden="true">
      <polygon points="0,0 806,0 792,27 806,54 0,54 14,27" fill="var(--green)"/>
    </svg>
    <ul>
      <li><a href="#" class="current">HOME</a></li>
      <li><a href="#">ABOUT US</a></li>
      <li><a href="#">WHY WE ARE?</a></li>
      <li><a href="#">SUCCESS STORIES</a></li>
      <li><a href="#">PARTNERS</a></li>
      <li><a href="#">NORVIK HOLDINGS</a></li>
    </ul>
  </nav>

  <header class="welcome">
    <h1>WELCOME TO $5 QUEST</h1>
    <p>Lorem ipsum dolor sit amet, consectetur adipiscing elit. Curabitur eu nisl odio. Cras egestas turpis in mi feugiat vel tincidunt arcu accumsan. Phasellus non posuere eros. Aenean consectetur.</p>
  </header>

  <div class="video-frame">
    <div class="play-button">
      <svg width="38" height="52" viewBox="0 0 38 52"><path d="M0 0 L38 26 L0 52 Z" fill="#e8e8e8"/></svg>
    </div>
    <div class="video-label">WATCH VIDEO</div>
  </div>

  <div class="cta-rule"></div>
  <a href="#" class="cta-button">
    <svg viewBox="0 0 349 52" width="349" height="52" aria-hidden="true">
      <polygon points="0,0 349,0 337,26 349,52 0,52 12,26" fill="var(--lime-light)"/>
      <polygon points="8,5 341,5 331,26 341,47 8,47 18,26" fill="var(--lime)"/>
    </svg>
    <span>ACCEPT THE CHALLENGE</span>
  </a>

  <footer class="site-footer">
    <div class="footer-brand"><span class="brand-dot"></span><span class="brand-name">$5 Quest</span></div>
    <small>All Rights reserved @ $5quest</small>
  </footer>
</div>
</body>
</html>
```